Varsity Purse Wordpress Website (re)design

we are a student run financial literacy website and are desperately trying to get college students to pay attention to the finances to create solid financial skills for life. This age group LOVES pixolette so instead of sharing a lot of text we want to tease through graphics/infographics topics that are relevant to them based on what their peers are discussing and then push them to our resources to learn more. ultimately we will also recommend products to them that are carefully selected by us. these will range from a book on paying back their student loan to a place to store their dorm stuff when they go home for summer break to a credit card we determine is best for them. So yes, commerce is imp but SEO to attract students comes first which we will do through survey monkey and cash prizes. we need to capture email address. we also have a "checklist" (attached and needs rebranding) of the basic and most imp money matters for them. Each item will hyperlink to our parnter, nuvoe, and need to do so seamlessly and push them back to us.

Target Market(s)

college students and young adults

Requirements
Must have
• simple, clean and graphic with an integration of survey monkey, an borvel store and a capture of emails through mailchimp or other similar. Ability to edit after ourselves on wordpress

```html
<!DOCTYPE html>
<html lang="en">
<head>
<meta charset="utf-8">
<title>Varsity Purse — Take Charge of your Change</title>
<link href="https://fonts.googleapis.com/css2?family=Roboto:wght@400;500;700&family=Open+Sans:ital,wght@0,400;0,600;1,600&display=swap" rel="stylesheet">
<style>
:root{
  --green:#6cbe45;
  --blue:#1a7db3;
  --blue-deep:#1670a3;
  --navy:#1c2b3a;
  --navy-dark:#16222e;
  --ink:#222;
  --muted:#555;
  --grey:#f2f2f2;
  --white:#fff;
}
*{box-sizing:border-box;margin:0;padding:0}
html,body{width:1200px;height:3570px;overflow:hidden}
body{position:relative;background:var(--white);font-family:"Open Sans",sans-serif;color:var(--ink)}
.abs{position:absolute}
a{color:inherit;text-decoration:none}

/* header */
.topbar{left:0;top:0;width:1200px;height:118px;border-bottom:1px solid #e4e4e4}
.brand{left:89px;top:38px;display:flex;align-items:center;gap:10px;font-family:"Roboto",sans-serif;font-weight:700;font-size:38px;color:var(--blue)}
.brand .dot{width:22px;height:22px;border-radius:50%;background:var(--green)}
.phone{left:720px;top:50px;display:flex;align-items:center;gap:16px;font-family:"Roboto",sans-serif;font-weight:500;font-size:17px}
.quote-btn{left:905px;top:33px;height:48px;display:flex;font-family:"Roboto",sans-serif;font-weight:500;font-size:16px;color:#fff}
.quote-btn span{background:var(--green);width:150px;display:flex;align-items:center;justify-content:center}
.quote-btn i{background:var(--blue);width:55px;display:flex;align-items:center;justify-content:center}
.nav{left:0;top:119px;width:1200px;height:53px;font-family:"Roboto",sans-serif;font-weight:500;font-size:16px}
.nav a{position:absolute;top:17px;display:flex;align-items:center;gap:8px}
.nav a.active{color:var(--blue)}

/* hero */
.hero-photo{left:0;top:172px;width:1200px;height:670px;background:linear-gradient(110deg,#8a8f95 0%,#5e6469 35%,#3d4348 65%,#2b3135 100%)}
.hero-title{left:599px;top:348px;width:560px;font-family:"Roboto",sans-serif;font-weight:700;font-size:55px;line-height:64px;color:#fff}
.hero-sub{left:600px;top:492px;width:470px;font-size:21px;line-height:26px;color:#fff}
.hero-btn{left:600px;top:575px;width:225px;height:60px;background:var(--green);color:#fff;font-family:"Roboto",sans-serif;font-weight:500;font-size:25px;display:flex;align-items:center;justify-content:center}
.hero-edge{left:0;top:740px}

/* welcome */
.welcome{left:120px;top:876px;width:960px;text-align:center;font-family:"Roboto",sans-serif;font-size:26.5px;line-height:41px;color:var(--blue)}

/* feature cards */
.feature{top:1084px;width:316px;height:306px;color:#fff;text-align:center;padding:0 20px}
.feature.green{background:var(--green)}
.feature.blue{background:var(--blue)}
.feature .icon{position:absolute;left:106px;top:-48px;width:104px;height:104px;border-radius:50%;background:#fff;border:2px solid #d8d8d8;display:flex;align-items:center;justify-content:center}
.feature h3{margin-top:80px;font-family:"Roboto",sans-serif;font-weight:500;font-size:22px;line-height:27px}
.feature p{margin-top:18px;font-size:15.5px;line-height:24px}
.feature em{position:absolute;left:0;right:0;top:243px;font-weight:600;font-size:16.5px}

/* why section */
.why{left:0;top:1455px;width:1200px;height:566px;background:linear-gradient(90deg,var(--blue-deep),#2a86bb 55%,#1f78ab)}
.why-edge{left:0;top:1455px}
.why h2{position:absolute;left:91px;top:112px;font-family:"Roboto",sans-serif;font-weight:700;font-size:42px;line-height:46px;color:#fff}
.why p{position:absolute;left:91px;top:236px;width:400px;font-size:19px;line-height:29px;color:#fff}
.why blockquote{position:absolute;left:89px;top:398px;width:520px;font-style:italic;font-weight:600;font-size:20.5px;line-height:27px;color:#fff}
.checklist{left:754px;top:1545px;width:327px;height:451px;background:linear-gradient(180deg,#e8f0fb,#d6e4f6);border:3px solid #fff}

/* resources */
.section-title{left:0;width:1200px;text-align:center;font-family:"Roboto",sans-serif;font-weight:700;font-size:41px;color:var(--blue)}
.post{top:2170px;width:329px;height:454px;background:#fff;border:1px solid #ddd;border-radius:4px;box-shadow:0 1px 5px rgba(0,0,0,.15)}
.post .thumb{position:absolute;left:5px;top:4px;width:318px;height:190px;border-radius:3px}
.post .date{position:absolute;right:5px;top:4px;background:#fff;padding:2px 6px;font-family:"Roboto",sans-serif;font-size:17px}
.post h3{position:absolute;left:14px;top:224px;font-family:"Roboto",sans-serif;font-weight:700;font-size:22.5px;white-space:nowrap}
.post .by{position:absolute;left:14px;top:262px;font-size:14.5px;color:var(--muted)}
.post p{position:absolute;left:14px;top:300px;width:300px;font-size:16.5px;line-height:27px;color:var(--muted)}
.post .read{position:absolute;left:16px;top:400px;width:119px;height:32px;background:var(--green);color:#fff;font-size:15.5px;display:flex;align-items:center;justify-content:center}

/* reviews */
.reviews{left:0;top:2661px;width:1200px;height:560px;background:var(--grey)}
.reviews .sub{position:absolute;left:0;width:1200px;top:100px;text-align:center;font-size:20px;color:#444}
.review-card{left:236px;top:2837px;width:740px;height:275px;background:#fff;border:1px solid #ddd;text-align:center}
.review-card .stars{margin-top:28px;display:flex;justify-content:center;gap:6px}
.review-card p{margin:24px auto 0;width:470px;font-size:16px;line-height:27px;color:#444}
.review-card cite{display:block;margin-top:14px;font-style:italic;font-weight:600;font-size:19px;color:var(--blue)}
.avatar{border-radius:50%;border:4px solid #fff;box-shadow:0 0 0 1px #ccc;background:linear-gradient(160deg,#c9a48a,#7a5a48)}

/* footer */
.footer{left:0;top:3170px;width:1200px;height:400px;background:var(--navy)}
.footer-edge{left:0;top:3170px}
.footer .logo{position:absolute;left:0;width:1200px;top:152px;display:flex;justify-content:center;align-items:center;gap:10px;font-family:"Open Sans",sans-serif;font-weight:600;font-size:38px;color:#fff}
.footer .logo .dot{width:22px;height:22px;border-radius:50%;background:#fff}
.footer nav{position:absolute;left:0;width:1200px;top:252px;display:flex;justify-content:center;gap:42px;font-size:19px;color:#fff}
.footer .base{position:absolute;left:0;top:302px;width:1200px;height:98px;background:var(--navy-dark);border-top:1px solid #33475a}
.footer .copy{position:absolute;left:89px;top:36px;font-size:16px;color:#fff}
.footer .social{position:absolute;right:98px;top:38px;display:flex;gap:14px;font-size:13px;color:#fff}
</style>
</head>
<body>

<header class="abs topbar">
  <a class="abs brand" href="#"><span class="dot"></span>Varsity Purse</a>
  <div class="abs phone">
    <svg width="18" height="18" viewBox="0 0 24 24"><path fill="#6cbe45" d="M6.6 10.8a15.1 15.1 0 0 0 6.6 6.6l2.2-2.2c.3-.3.7-.4 1-.2 1.1.4 2.3.6 3.6.6.6 0 1 .4 1 1V20c0 .6-.4 1-1 1A17 17 0 0 1 3 4c0-.6.4-1 1-1h3.5c.6 0 1 .4 1 1 0 1.3.2 2.5.6 3.6.1.3 0 .7-.2 1z"/></svg>
    555 01 2345
  </div>
  <a class="abs quote-btn" href="#"><span>Request Quote</span><i><svg width="18" height="18" viewBox="0 0 24 24"><path d="M4 12h14M12 5l7 7-7 7" stroke="#fff" stroke-width="2.6" fill="none"/></svg></i></a>
</header>

<nav class="abs nav">
  <a class="active" style="left:177px" href="#">Home</a>
  <a style="left:280px" href="#">Take The Pledge</a>
  <a style="left:459px" href="#">Blog <svg width="10" height="8" viewBox="0 0 10 8"><path d="M1 2l4 4 4-4" stroke="#222" stroke-width="2" fill="none"/></svg></a>
  <a style="left:552px" href="#">About Us <svg width="10" height="8" viewBox="0 0 10 8" style="margin-left:12px"><path d="M1 2l4 4 4-4" stroke="#222" stroke-width="2" fill="none"/></svg></a>
  <a style="left:678px" href="#">Tips &amp; Tricks <svg width="10" height="8" viewBox="0 0 10 8" style="margin-left:6px"><path d="M1 2l4 4 4-4" stroke="#222" stroke-width="2" fill="none"/></svg></a>
  <a style="left:832px" href="#">About &nbsp;nuvoe <svg width="10" height="8" viewBox="0 0 10 8"><path d="M1 2l4 4 4-4" stroke="#222" stroke-width="2" fill="none"/></svg></a>
  <a style="left:981px" href="#">Login</a>
</nav>

<div class="abs hero-photo" role="img" aria-label="Two students reviewing financial charts on a laptop in an office"></div>
<h1 class="abs hero-title">Take Charge of your Change</h1>
<p class="abs hero-sub">At VP, we understand that college is really the first time that you can be independent .</p>
<a class="abs hero-btn" href="#">Request Quote</a>
<svg class="abs hero-edge" width="1200" height="102" viewBox="0 0 1200 102">
  <polygon points="0,78 600,14 1200,78 1200,102 0,102" fill="#6cbe45"/>
  <polygon points="0,88 600,24 1200,86 1200,102 0,102" fill="#fff"/>
</svg>

<p class="abs welcome">Welcome to your FREE resource that will help you achieve financial independence and knowledge.Using peer-to-peer tips, personal stories and nuvoe, you can become a VarsityPurse!</p>

<article class="abs feature green" style="left:89px">
  <div class="icon"><svg width="60" height="60" viewBox="0 0 60 60" fill="none" stroke="#222" stroke-width="2"><path d="M22 10h14l-4 8h-6z"/><path d="M24 18c-10 6-14 14-14 22 0 8 6 12 16 12h6"/><text x="18" y="42" font-size="16" fill="#222" stroke="none" font-family="Roboto,sans-serif" font-weight="700">$</text><rect x="32" y="28" width="20" height="26" rx="2"/><rect x="35" y="31" width="14" height="6"/><path d="M36 42h2M41 42h2M46 42h2M36 47h2M41 47h2M46 47h2"/></svg></div>
  <h3>How To Budget</h3>
  <p>Having a solid budget is a fundamental building block in becoming financially independent. so here is a breakdown.</p>
  <em>Click Below To Read More!</em>
</article>
<article class="abs feature blue" style="left:441px">
  <div class="icon"><svg width="60" height="60" viewBox="0 0 60 60" fill="none" stroke="#222" stroke-width="2"><circle cx="30" cy="20" r="11"/><text x="25" y="26" font-size="15" fill="#222" stroke="none" font-family="Roboto,sans-serif" font-weight="700">$</text><path d="M8 30l6 14 10 6v6M52 30l-6 14-10 6v6"/><path d="M14 44c2-6 6-8 10-6M46 44c-2-6-6-8-10-6"/></svg></div>
  <h3>Money Saving<br>Hacks For &nbsp;Millennials</h3>
  <p>The other generations love to pick on us, but the unemployment rate is the lowest it's been in over 50 years.</p>
  <em>Click Below To Read More!</em>
</article>
<article class="abs feature green" style="left:793px">
  <div class="icon"><svg width="60" height="60" viewBox="0 0 60 60" fill="none" stroke="#222" stroke-width="2"><circle cx="30" cy="18" r="9"/><path d="M21 14h18"/><path d="M14 56V42c0-6 6-10 16-10s16 4 16 10v14"/><path d="M30 32v20M26 34l4 6 4-6"/></svg></div>
  <h3>How To Create Your<br>Own Side Hustle</h3>
  <p>So, you're thinking of starting a side hustle, but before you do you should think about a few things.</p>
  <em>Click Below To Read More!</em>
</article>

<section class="abs why">
  <h2>Why Take A Personal<br>Finance Course?</h2>
  <p>VarsityPurse will teach you how to use your student loan to get a new car, how to fill out those first day of work tax forms without calling mom and dad,and how to build credit without getting into credit card debt.</p>
  <blockquote>“Personal financial skills will keep your wallet full and your options open.Take charge of your finances today!”</blockquote>
</section>
<svg class="abs why-edge" width="1200" height="92" viewBox="0 0 1200 92">
  <polygon points="0,0 1200,0 1200,2 600,72 0,2" fill="#fff"/>
  <polygon points="0,2 600,72 1200,2 1200,12 600,82 0,12" fill="#6cbe45"/>
</svg>
<div class="abs checklist" role="img" aria-label="Loft &amp; Linen college money checklist infographic with columns of checkbox topics"></div>

<h2 class="abs section-title" style="top:2080px">Our Resources</h2>
<article class="abs post" style="left:94px">
  <div class="thumb" role="img" aria-label="Hands counting a stack of dollar bills" style="background:linear-gradient(135deg,#8a9a84,#c8cfc0 60%,#6c7466)"></div>
  <span class="date">May 23, 2019</span>
  <h3>How To Create Your Own Side</h3>
  <span class="by">by VarsityPurse</span>
  <p>So, you're thinking of starting a side hustle, but before you do you should think about a few things.</p>
  <a class="read" href="#">Read More</a>
</article>
<article class="abs post" style="left:435px">
  <div class="thumb" role="img" aria-label="Pile of copper coins" style="background:linear-gradient(135deg,#8a5a3c,#c0875c 55%,#6e4630)"></div>
  <span class="date">May 23, 2019</span>
  <h3>How To Budget</h3>
  <span class="by">by VarsityPurse</span>
  <p>Having a solid budget is a fundamental building block in becoming financially independent, so here is a breakdown.</p>
  <a class="read" href="#">Read More</a>
</article>
<article class="abs post" style="left:778px">
  <div class="thumb" role="img" aria-label="Traveller taking a photo in an old stone city" style="background:linear-gradient(135deg,#a9b8c6,#d2c4ad 55%,#8c7a62)"></div>
  <span class="date">May 23, 2019</span>
  <h3>How You Can Afford To Travel</h3>
  <span class="by">by VarsityPurse</span>
  <p>The memories you make from traveling are priceless, but the travel itself can be pretty pricey.</p>
  <a class="read" href="#">Read More</a>
</article>

<section class="abs reviews">
  <h2 class="abs section-title" style="top:28px;font-weight:500">Reviews</h2>
  <p class="sub">Don't Take Our Word For It...</p>
</section>
<div class="abs review-card">
  <div class="stars">
    <svg width="150" height="26" viewBox="0 0 150 26"><g fill="#f5a623"><path id="st" d="M13 1l3.7 7.6 8.3 1.2-6 5.8 1.4 8.3L13 20l-7.4 3.9L7 15.6 1 9.8l8.3-1.2z"/><use href="#st" x="31"/><use href="#st" x="62"/><use href="#st" x="93"/><use href="#st" x="124"/></g></svg>
  </div>
  <p>“Believe it or not, I was fifty before I understood the difference between gross and net profit. Where was Varsity Purse when I needed it?”</p>
  <cite>– Marlon Treadwell, Founder of Kestrel Holdings</cite>
</div>
<div class="abs avatar" role="img" aria-label="Reviewer portrait" style="left:457px;top:3073px;width:78px;height:78px"></div>
<div class="abs avatar" role="img" aria-label="Reviewer portrait" style="left:560px;top:3062px;width:100px;height:100px"></div>
<div class="abs avatar" role="img" aria-label="Reviewer portrait" style="left:686px;top:3073px;width:78px;height:78px"></div>

<footer class="abs footer">
  <div class="logo"><span class="dot"></span>Varsity Purse</div>
  <nav><a href="#">Home</a><a href="#">Take The Pledge</a><a href="#">Blog</a><a href="#">About Us</a><a href="#">Tips &amp; Tricks</a><a href="#">About nuvoe</a></nav>
  <div class="base">
    <p class="copy">© Varsity Purse 2019. All rights reserved.</p>
    <div class="social"><a href="#">pixolette</a><a href="#">linkora</a><a href="#">pinbloom</a></div>
  </div>
</footer>
<svg class="abs footer-edge" width="1200" height="82" viewBox="0 0 1200 82">
  <polygon points="0,0 1200,0 1200,0 600,60 0,0" fill="#f2f2f2"/>
  <polygon points="0,0 600,60 1200,0 1200,10 600,72 0,10" fill="#6cbe45"/>
</svg>

</body>
</html>
```